Structural Engineering Business Card

Brookvane Drafting does residential house plans for clients in Central Florida. Would like simple but elegant business card that is appropriate for a house plan engineering company. Prefer black business card with black/white them but open to other shades of blue. I uploaded a sample card that I came across that looked good but please come up with your own creative designs.

Contact Information for Business Card

Name, Title, Phone, Email, Address, website

```html
<!DOCTYPE html>
<html lang="en">
<head>
<meta charset="UTF-8">
<title>Brookvane Drafting – Business Card</title>
<link rel="stylesheet" href="https://fonts.googleapis.com/css2?family=Open+Sans:wght@300;400;600;800&display=swap">
<style>
  :root {
    --stage: #2a2a2a;
    --card: #1c1c1c;
    --ink: #ffffff;
    --ink-soft: #cfcfcf;
    --ink-muted: #9a9a9a;
  }
  * { box-sizing: border-box; margin: 0; padding: 0; }
  html, body {
    width: 1200px; height: 900px; overflow: hidden;
    background: var(--stage);
    font-family: "Open Sans", sans-serif;
    color: var(--ink);
  }
  .stage {
    position: relative; width: 1200px; height: 900px;
    display: flex; align-items: center; justify-content: center; gap: 40px;
  }
  .card {
    position: relative;
    width: 540px; height: 309px;
    background: var(--card);
    border-radius: 18px;
    box-shadow: 0 20px 40px rgba(0,0,0,0.45);
  }
  .wordmark {
    font-weight: 800;
    font-size: 34px;
    letter-spacing: 0.5px;
    line-height: 1;
    color: var(--ink);
    display: flex; align-items: center; gap: 12px;
    text-transform: uppercase;
    white-space: nowrap;
  }
  .wordmark-square { width: 18px; height: 18px; background: var(--ink); flex: none; }
  .card-back .wordmark {
    position: absolute; left: 50%; top: 50%; transform: translate(-50%, -50%);
  }
  .card-front .wordmark {
    position: absolute; right: 36px; bottom: 30px; font-size: 24px; gap: 10px;
  }
  .card-front .wordmark-square { width: 14px; height: 14px; }
  .contact { position: absolute; left: 36px; top: 30px; }
  .person-name { font-size: 17px; font-weight: 600; letter-spacing: 0.5px; color: var(--ink-soft); text-transform: uppercase; }
  .person-title { font-size: 10px; letter-spacing: 1px; color: var(--ink-muted); text-transform: uppercase; margin-top: 2px; }
  .address { margin-top: 18px; font-size: 12px; font-weight: 300; line-height: 1.5; color: var(--ink-soft); }
  .lines { margin-top: 18px; list-style: none; font-size: 12px; font-weight: 300; color: var(--ink-soft); }
  .lines li { display: flex; align-items: center; gap: 7px; line-height: 1.7; }
  .lines svg { width: 10px; height: 10px; fill: none; stroke: var(--ink-soft); stroke-width: 1.6; }
</style>
</head>
<body>
  <main class="stage">
    <section class="card card-front" aria-label="Card front">
      <div class="contact">
        <p class="person-name">Daniel Hart</p>
        <p class="person-title">Director</p>
        <p class="address">418 Cedar Lane<br>Orlando, FL 32801</p>
        <ul class="lines">
          <li><svg viewBox="0 0 12 12"><path d="M3 1l2 2.5-1.2 1.3a7 7 0 0 0 3.4 3.4L8.5 7 11 9l-1.3 1.8C5.5 10.5 1.5 6.5 1.2 2.3z"/></svg>407.555.0192</li>
          <li><svg viewBox="0 0 12 12"><rect x="1" y="2.5" width="10" height="7"/><path d="M1 2.5l5 4 5-4"/></svg>info@brookvane.com</li>
          <li><svg viewBox="0 0 12 12"><circle cx="6" cy="6" r="5"/><path d="M1 6h10M6 1c-2.5 3-2.5 7 0 10M6 1c2.5 3 2.5 7 0 10"/></svg>www.brookvane.com</li>
        </ul>
      </div>
      <div class="wordmark"><span class="wordmark-square"></span>Brookvane Drafting</div>
    </section>
    <section class="card card-back" aria-label="Card back">
      <div class="wordmark"><span class="wordmark-square"></span>Brookvane Drafting</div>
    </section>
  </main>
</body>
</html>
```